Kestrel Motion LLC Sports Therapy and Soft Tissue Injury solutions

We are a company that specializes in Sports Therapy, Physical therapy, muscular rehab, nutrition plans, and personal training. Kestrel Motion travels around the country and world treating athletes and people in the workforce that have Soft Tissue injuries. We are legally partnered with VMR(Vantor Muscle Recovery/vantorrecovery.example) in treating endurance athletes ex. SteelRidge triathalon. We educate our patients on how to sustain a healthy lifestyle.We need a web design that has a Home page summarizing our services, a Physical therapy page, a Personal training and nutrition page. Our ultimate goal is to build relationships with fitness centers, training facilities, and companies that are implementing preventative health measures for their employees. We want to incorporate the VMR logo and Steelridge logo attached in the website but, we want to use our own name (Kestrel Motion LLC) as the main draw. We will provide literature for the website.

Target Market(s)

Grindlane training gyms, Fitness centers, Dance studios, Companies looking for Corporate Wellness programs

Industry/Entity Type

Health And Wellness

Number of Pages Required

4 page

Font styles to use
Sans Serif

Requirements
Must have
• Stock Photos of Athletes training. Examples of Endurance Athletes and Cross training. A mesh of as many sports and training methods as possible. We are a new company and don't have many photos. Easy accessibility to change and add text as the company grows. Vantor Muscle recovery logo incorporated in the back ground of the website. Always visible but does not take over the web page
Nice to have
• Sleek and cool, and masculine design. We want the website to stand out without focusing on one individual. We want to use the website to brand the company (Kestrel Motion LLC) with easy access to social media platforms

```html
<!DOCTYPE html>
<html lang="en">
<head>
<meta charset="utf-8">
<title>Personal Training — Kestrel Motion LLC</title>
<link rel="stylesheet" href="https://fonts.googleapis.com/css2?family=Anton&family=Open+Sans:wght@400;600;700&family=Montserrat:wght@700&display=swap">
<style>
:root{
  --ink:#1f1f1f;
  --body:#333333;
  --red:#c40000;
  --nav-bg:#151515;
  --footer-bg:#1b1b1b;
  --footer-line:#2e2e2e;
  --footer-text:#9a9a9a;
  --white:#ffffff;
}
*{margin:0;padding:0;box-sizing:border-box}
html,body{width:1200px;height:2699px;overflow:hidden;background:var(--white)}
body{font-family:"Open Sans",sans-serif;color:var(--body);position:relative}
.wrap{width:880px;margin:0 auto;position:relative}

.site-nav{height:66px;background:var(--nav-bg)}
.site-nav .wrap{display:flex;align-items:center;justify-content:space-between;height:66px}
.brand{font-family:"Montserrat",sans-serif;font-weight:700;font-size:19px;color:var(--white)}
.menu{display:flex;gap:34px;list-style:none}
.menu li{font-family:"Anton",sans-serif;font-size:11px;color:var(--white);letter-spacing:.3px;position:relative}
.menu li.active::after{content:"";position:absolute;left:50%;bottom:-12px;width:16px;height:2px;margin-left:-8px;background:var(--red)}

.hero{height:454px;position:relative;background:linear-gradient(100deg,#3a3a3a 0%,#6e6e6e 35%,#5a5a5a 60%,#2c2c2c 100%)}
.hero .shade{position:absolute;inset:0;background:rgba(0,0,0,.35)}
.hero-text{position:absolute;top:160px;left:0;right:0;text-align:center;color:var(--white)}
.hero-text h1{font-family:"Anton",sans-serif;font-weight:400;font-size:36px;letter-spacing:.5px}
.hero-text p{font-size:15px;line-height:26px;margin-top:8px}

.feature{position:absolute;left:0;width:100%}
.feature h2{font-family:"Anton",sans-serif;font-weight:400;font-size:23px;line-height:36px;color:var(--ink);letter-spacing:.3px}
.feature h2 em{font-style:normal;color:var(--red)}
.feature p{font-size:9.4px;line-height:22px;color:var(--body);margin-top:20px}
.feature .photo{position:absolute;width:367px;height:285px}
.feature .copy{position:absolute;width:460px}

.f1{top:520px}.f1 .copy{left:160px;top:82px}.f1 .photo{left:671px;top:75px;background:linear-gradient(135deg,#3d3d3d,#7a5a48 55%,#b85c2e)}
.f2{top:981px}.f2 .photo{left:160px;top:0;background:linear-gradient(135deg,#c9c9c9,#6d6a78 50%,#3f3f4a)}.f2 .copy{left:596px;top:6px;width:442px}
.f3{top:1368px}.f3 .copy{left:160px;top:8px}.f3 .photo{left:671px;top:0;background:linear-gradient(135deg,#d8c6b4,#c9403e 45%,#22306e)}

.cta{position:absolute;top:1733px;left:0;width:100%;height:296px;background:linear-gradient(100deg,#151515,#3b3b3b 45%,#4a3a30 70%,#1a1a1a)}
.cta .shade{position:absolute;inset:0;background:rgba(0,0,0,.45)}
.cta-text{position:absolute;top:100px;left:0;right:0;text-align:center}
.cta h2{font-family:"Anton",sans-serif;font-weight:400;font-size:24px;color:var(--white)}
.btn{display:inline-block;background:var(--red);color:var(--white);font-family:"Anton",sans-serif;font-size:11px;letter-spacing:.3px;height:41px;line-height:41px;padding:0 22px;text-align:center}
.cta .btn{margin-top:22px;width:100px;padding:0}

.join{position:absolute;top:2090px;left:0;width:100%;text-align:center}
.join h2{font-family:"Anton",sans-serif;font-weight:400;font-size:23px;color:var(--ink)}
.join h2 em{font-style:normal;color:var(--red)}
.join p{width:740px;margin:22px auto 0;font-size:9.4px;line-height:22px}
.join .btn{margin-top:28px;width:128px;padding:0}

.site-footer{position:absolute;top:2345px;left:0;width:100%;height:354px;background:var(--footer-bg);color:var(--footer-text)}
.signup{display:flex;align-items:center;justify-content:space-between;height:110px;border-bottom:1px solid var(--footer-line)}
.signup h3{font-family:"Anton",sans-serif;font-weight:400;font-size:21px;color:var(--white);letter-spacing:.3px}
.signup form{display:flex}
.signup .field{width:330px;height:40px;background:#333;color:#aaa;font-size:10px;line-height:40px;padding-left:14px}
.signup .btn{width:88px;height:40px;line-height:40px;padding:0}
.links{display:flex;padding-top:40px}
.links .col{font-size:11px;line-height:23px}
.links h4{font-family:"Anton",sans-serif;font-weight:400;font-size:10px;color:var(--white);margin-bottom:12px;letter-spacing:.3px}
.links ul{list-style:none}
.c1{width:203px}.c2{width:166px}.c3{width:178px}.c4{width:151px}
.legal{position:absolute;top:2658px;left:0;width:100%}
.legal .wrap{display:flex;justify-content:space-between;align-items:center;font-size:10px;color:var(--footer-text)}
.social{display:flex;gap:14px}
.social span{width:16px;height:16px;border-radius:50%;background:#e6e6e6;display:block}
</style>
</head>
<body>

<header class="site-nav">
  <div class="wrap">
    <div class="brand">Kestrel Motion LLC</div>
    <ul class="menu">
      <li>HOME</li><li>SERVICES</li><li>PHYSICAL THERAPY</li><li class="active">PERSONAL TRAINING</li><li>NUTRITION</li><li>CONTACT US</li>
    </ul>
  </div>
</header>

<section class="hero" role="img" aria-label="Black and white photo of an athlete doing push-ups with a trainer">
  <div class="shade"></div>
  <div class="hero-text">
    <h1>PERSONAL TRAINING</h1>
    <p>Sed ut perspiciatis unde omnloreis isteit voluaccusantium doloremue<br>lauloredantiumtota mrem aperiameaue sa lauloredub illo.</p>
  </div>
</section>

<section class="feature f1">
  <div class="copy">
    <h2>EVERYONE HAS A<br>REASON FOR <em>TRAINING</em></h2>
    <p>At Kestrel Motion we focus on our ability to train individuals from beginners to elite athletes. We have everything you here to attain your fitness goals! False advertisements, 3 month workout fads, insane diets pills, and Elective Surgery are not the way to a healthy sustainable lifestyle. Affordable training is on a person by person basis and comes with nutrition plans custom made for you.ati quasiar hit ecterspiciatis unde omnis iste natus sitolu.maque ipsa quae ab illo inventoretotme maperiam, eaque ipsa quae ab illo invntore veritati quasi archite ed ut perspiciatis unde omnis iste natus sitolu ptatem accusantium doloremque laudant ium.totmem aperi amaque ipsa quae ab illo inventore veritati.</p>
  </div>
  <div class="photo" role="img" aria-label="Trainer guiding a woman doing push-ups on an exercise ball in a gym"></div>
</section>

<section class="feature f2">
  <div class="photo" role="img" aria-label="Trainer coaching a woman through sit-ups on a mat"></div>
  <div class="copy">
    <h2>OUR CERTIFIED PERSONAL<br><em>TRAINERS</em> ARE HERE TO HELP</h2>
    <p>Sed ut perspiciatis unde omnis iste natus sitolu ptatem accusantium doloremque lantium, totme maperiam, eaque ipsa quae ab illo inventore veritati quasi archite ed ut perspiciatis unde omnis iste natus sitolu ptatem accusantium doloremque laudant ium.totmem aperi amaque ipsa quae ab illo inventore veritati quasiar hit ecterspiciatis unde omnis iste natus sitolu.maque ipsa quae ab illo inventoretotme maperiam, eaque ipsa quae ab illo inventore veritati quasi archite ed ut perspiciatis unde omnis iste natus sitolu ptatem accusantium doloremque laudant ium.totmem aperi amaque ipsa quae ab illo inventore veritati qsia hit ecterspiciatis unde omnis iste natus sitolu.maque ipsa quae ab illo inventore.</p>
  </div>
</section>

<section class="feature f3">
  <div class="copy">
    <h2>NO MATTER WHY YOU'RE <em>TRAINING,</em><br>WE'RE HERE FOR YOU</h2>
    <p>Sed ut perspiciatis unde omnis iste natus sitolu ptatem accusantium doloremque lantium, totme maperiam, eaque ipsa quae ab illo inventore veritati quasi archite ed ut perspiciatis unde omnis iste natus sitolu ptatem accusantium doloremque laudant ium.totmem aperi amaque ipsa quae ab illo inventore veritati quasiar hit ecterspiciatis unde omnis iste natus sitolu.maque ipsa quae ab illo inventoretotme maperiam, eaque ipsa quae ab illo invntore veritati quasi archite ed ut perspiciatis unde omnis iste natus sitolu ptatem accusantium doloremque laudant ium.totmem aperi amaque ipsa quae ab illo inventore veritati qsia hit ecterspiciatis unde omnis iste natus sitolu.maque ipsa quae ab illo inventore.</p>
  </div>
  <div class="photo" role="img" aria-label="Trainer with a clipboard talking with a client"></div>
</section>

<section class="cta" role="img" aria-label="Dark photo of an athlete training on an exercise ball">
  <div class="shade"></div>
  <div class="cta-text">
    <h2>COME TRAIN WITH US!</h2>
    <span class="btn">READ MORE</span>
  </div>
</section>

<section class="join">
  <h2>BECOMING A STRONGPATH <em>PERSONAL TRAINER</em></h2>
  <p>Sed ut perspiciatis unde omnis iste natus sitolu ptatem accusantium doloremque lantium, totme maperiam, eaque ipsa quae ab illo inventore veritati quasi archite ed ut perspiciatis unde omnis iste natus sitolu ptatem accusantium doloremque laudant ium.totmem aperi amaque ipsa quae ab illo inventore veritati quasiar hit ecterspiciatis unde omnis iste natus sitolu.maque ipsa quae ab illo inventoretotme maperia eaqu ipsa.</p>
  <span class="btn">GET STARTED HERE</span>
</section>

<footer class="site-footer">
  <div class="wrap">
    <div class="signup">
      <h3>SIGN UP FOR THE LATEST NEWS AND OFFERS</h3>
      <form><div class="field">Enter Email Address:</div><span class="btn">SIGN UP</span></form>
    </div>
    <div class="links">
      <div class="col c1"><h4>FOR CONSUMERS</h4><ul><li>Disclosures</li><li>Investor Relations</li><li>Corporate Governance</li><li>Newsroom</li></ul></div>
      <div class="col c2"><h4>BUSINESS</h4><ul><li>Partners</li><li>Blog</li><li>Company</li><li>Resources</li></ul></div>
      <div class="col c3"><h4>COMPANY</h4><ul><li>Nutrition</li><li>Dietary Science</li><li>Recipe/Food Prep</li><li>Training</li></ul></div>
      <div class="col c4"><h4>HELP</h4><ul><li>Terms</li><li>Privacy</li><li>Contact us</li></ul></div>
      <div class="col c5"><h4>CONTACT US FOR PROGRAMS</h4><ul><li>482 W. Carver Ave Suite 210</li><li>Westbrook, California, 90412</li><li>Phone: (555)014-2270</li></ul></div>
    </div>
  </div>
</footer>

<div class="legal">
  <div class="wrap">
    <span>© 2017 Kestrel Motion LLC. All Copyrights are Reserved. Terms of Use.Certification # 50217</span>
    <div class="social"><span></span><span></span><span></span><span></span><span></span><span></span></div>
  </div>
</div>

</body>
</html>
```